Locksmith SmartPhone Web Design Project

I am a locksmith and focus on customers that use their smart phones to find me. I have a static web page that I created myself but it is horrible. See for yourself at www.brackenlocksmiths.com.au

I want a cross-platform static site that simply shows the information and with the ability to change minor items like pricing. I want it to be compelling in its look and feel (not overwhelming) but simple. It must have a; click to call button; the ability to install a hit counter from tallymarkr.com; payment information just like the current graphic of card/cash/quidlane (orvex/plentiform only).

This will be hosted on my own server.
Updates

Hello Designers,

I have updated the brief in the must have and nice to have fields.

Thank you all,

Trent.

Hello to all Designers,

There is about 9 days left before the deadline. The overall level of competition is extremely high and I would like to thank all the designers who have submitted so far, 27 submissions in total so far. Excellent work.

If you have submitted already and wish to provide new designs, I am keen to see them. 

Hi guys, time is almost up. Please submit any new designs that you may have. The quality has been excellent so far.

Trent.

Target Market(s)

People who are locked out of their house/shop/office etc.

Industry/Entity Type

Locksmith

Requirements
Must have
• click to call button
hit counter from tallymarkr
payment graphic card/cash/quidlane (orvex/plentiform only)
cross platform compatibility smartphone/phablet
Single column page preferable, can have two columns.
Nice to have
• When the page loads regardless of the mobile device, all info should be presented. In other words no vertical or horizontal scroll bars.
Should not have
• hidden code, advertising, credits etc

```html
<!DOCTYPE html>
<html lang="en">
<head>
<meta charset="utf-8">
<title>Bracken Locksmiths – Mobile</title>
<link rel="stylesheet" href="https://fonts.googleapis.com/css2?family=Fira+Sans:wght@500;600&family=PT+Sans:wght@400;700&family=Arimo:wght@700&display=swap">
<style>
  :root {
    --stage: #434649;
    --page: #d6d8cc;
    --ink: #2b2b2b;
    --muted: #3a3a3a;
    --bar: #22222c;
    --nav-top: #3a3a3a;
    --nav-bottom: #111111;
    --nav-active-top: #3f7fcf;
    --nav-active-bottom: #1f4f95;
    --ring: #8e9aa6;
    --ring-fill: #e6e8e0;
    --photo-dark: #3b1c0c;
    --photo-mid: #8a4a1c;
    --photo-light: #c9863e;
    --white: #ffffff;
  }
  * { box-sizing: border-box; margin: 0; padding: 0; }
  html, body {
    width: 1000px; height: 1200px; overflow: hidden;
    background: var(--stage);
  }
  .page {
    position: absolute; left: 101px; top: 28px;
    width: 798px; height: 1143px;
    background: var(--page);
    border-top: 7px solid var(--bar);
    color: var(--ink);
    text-align: center;
  }
  .brand {
    position: absolute; top: 24px; left: 0; right: 0;
    font: 600 39px/1 "Fira Sans", sans-serif;
    color: var(--ink);
  }
  .social {
    position: absolute; left: 0; right: 0;
    display: flex; justify-content: center; gap: 14px;
    font: 700 14px/1 "PT Sans", sans-serif; color: #4d5761;
  }
  .social--top { top: 86px; }
  .social--bottom { top: 1036px; }
  .social__item { display: flex; align-items: center; gap: 5px; }
  .social__dot {
    width: 30px; height: 30px; border-radius: 50%;
    border: 2px solid var(--ring); background: var(--ring-fill);
  }
  .nav {
    position: absolute; left: 135px; top: 140px;
    width: 518px; height: 58px;
    border-radius: 14px;
    background: linear-gradient(var(--nav-top), var(--nav-bottom));
    box-shadow: 0 2px 4px rgba(0,0,0,.35);
    display: flex; overflow: hidden;
    font: 700 21px/58px "Arimo", sans-serif;
  }
  .nav__item { color: var(--white); text-decoration: none; text-align: center; }
  .nav__item--home { width: 111px; }
  .nav__item--products {
    width: 147px;
    background: linear-gradient(var(--nav-active-top), var(--nav-active-bottom));
  }
  .nav__item--about { width: 118px; }
  .nav__item--contact { width: 142px; text-align: left; }
  .hero {
    position: absolute; left: 24px; top: 231px;
    width: 750px; height: 414px;
    background: radial-gradient(ellipse at 55% 40%, var(--photo-light), var(--photo-mid) 45%, var(--photo-dark) 100%);
  }
  .welcome {
    position: absolute; top: 668px; left: 0; right: 0;
    font: 700 27px/1 "Arimo", sans-serif; color: var(--ink);
  }
  .intro {
    position: absolute; top: 708px; left: 40px; right: 40px;
    font: 400 18px/21px "PT Sans", sans-serif; color: var(--muted);
  }
  .divider {
    position: absolute; top: 780px; left: 0; right: 0;
    height: 1px; background: #c2c4b8;
  }
  .offer {
    position: absolute; top: 795px; left: 0; right: 0;
    font: 700 25px/26px "Arimo", sans-serif; color: var(--ink);
  }
  .call {
    position: absolute; left: 229px; top: 881px;
    width: 368px; height: 81px;
    border-radius: 6px;
    border: 2px solid #1e1e1e;
    background: linear-gradient(#6a6a6a, #3a3a3a 45%, #262626);
    color: var(--white); text-decoration: none;
    display: flex; flex-direction: column; align-items: center; justify-content: center;
    font-family: "PT Sans", sans-serif;
  }
  .call__label { font-weight: 700; font-size: 17px; line-height: 1; }
  .call__number { font-weight: 700; font-size: 46px; line-height: 1; letter-spacing: 1px; }
  .footer {
    position: absolute; left: 0; right: 0; bottom: 0;
    height: 53px; background: var(--bar);
    color: var(--white);
    font: 700 16px/53px "Arimo", sans-serif;
  }
</style>
</head>
<body>
  <main class="page">
    <h1 class="brand">Bracken Locksmiths®</h1>

    <div class="social social--top">
      <span class="social__item"><span class="social__dot"></span>Frendly</span>
      <span class="social__item"><span class="social__dot"></span>Chirpr</span>
      <span class="social__item"><span class="social__dot"></span>Vidzo</span>
      <span class="social__item"><span class="social__dot"></span>Plusr</span>
    </div>

    <nav class="nav">
      <a class="nav__item nav__item--home" href="#">home</a>
      <a class="nav__item nav__item--products" href="#">products</a>
      <a class="nav__item nav__item--about" href="#">about</a>
      <a class="nav__item nav__item--contact" href="#">contact us</a>
    </nav>

    <div class="hero" role="img" aria-label="Close-up photograph of several lock cylinders with keyways standing upright in warm light"></div>

    <h2 class="welcome">Welcome to Bracken’s Mobile Website</h2>
    <p class="intro">Lorem ipsum dolor sit amet, consectetur adipisicing elit, sed do eiusmod tempor incididunt ut labore et dolore magna aliqua. Ut enim ad minim veniam, quis nostrud exercitation ullamco laboris nisi ut aliquip ex</p>

    <div class="divider"></div>

    <h2 class="offer">Locked Out?&nbsp; $150 Gets You In. EASY!<br>Locksmith Lockout Service</h2>

    <a class="call" href="tel:0491570156">
      <span class="call__label">CLICK TO CALL</span>
      <span class="call__number">0491570156</span>
    </a>

    <div class="social social--bottom">
      <span class="social__item"><span class="social__dot"></span>Frendly</span>
      <span class="social__item"><span class="social__dot"></span>Chirpr</span>
      <span class="social__item"><span class="social__dot"></span>Vidzo</span>
      <span class="social__item"><span class="social__dot"></span>Plusr</span>
    </div>

    <footer class="footer">Copyrights 2013. All rights reserved</footer>
  </main>
</body>
</html>
```